Bayward Vale Physiotherapy Website www.baywardvalephysiotherapy.com.au

Create Wordpress website for Bayward Vale Physiotherapy which aligns with our other locations www.oakmerephysiotherapy,com.au. We would like the website to present in a similar fashion to our exisiting site with similar headings and layout. We will then alter the text to make it location specific.

Coding

Coded - Design and coding required

Number of Pages Required

1 page

Font styles to use
Sans Serif

Requirements
Must have
• Colours of the website must match the colours of the colour Bayward Vale Physiotherapy logo
• Website must be complimentary to existing websites,
• www.oakmerephysiotherapy.com.au
• www.oakmerepilatesandrehab.com.au

```html
<!DOCTYPE html>
<html lang="en">
<head>
<meta charset="utf-8">
<title>Bayward Vale Physiotherapy</title>
<link href="https://fonts.googleapis.com/css2?family=Open+Sans:wght@400;600;700&display=swap" rel="stylesheet">
<style>
:root{
  --teal:#7fb8a1;
  --teal-dark:#6aa78f;
  --navy:#26295a;
  --ink:#2f3350;
  --text:#5c6070;
  --grey-bg:#f1f1f1;
  --footer:#2b2b2b;
  --white:#ffffff;
}
*{box-sizing:border-box;margin:0;padding:0}
html,body{width:1200px;height:3600px;overflow:hidden}
body{font-family:"Open Sans",Arial,sans-serif;color:var(--text);background:var(--white);position:relative}
.wrap{width:936px;margin:0 auto;position:relative}

/* header */
.site-header{height:125px;position:relative}
.brand{position:absolute;left:132px;top:32px;display:flex;align-items:center;gap:12px}
.brand-dot{width:34px;height:34px;border-radius:50%;background:var(--navy)}
.brand-name{font-size:22px;font-weight:700;color:var(--navy);line-height:1.1;width:220px}
.search{position:absolute;left:548px;top:42px;width:192px;height:40px;border:1px solid #c9c9c9;display:flex;align-items:center;padding:0 12px;font-size:13px;color:#888;justify-content:space-between}
.contact-top{position:absolute;left:930px;top:36px;color:var(--ink)}
.contact-top .addr{font-size:13px;display:flex;align-items:center;gap:6px}
.contact-top .phone{font-size:22px;font-weight:700;display:flex;align-items:center;gap:8px;margin-top:6px}

/* nav */
.main-nav{height:40px;background:var(--teal)}
.main-nav ul{list-style:none;display:flex;height:40px;width:936px;margin:0 auto}
.main-nav li{color:var(--white);font-size:14px;font-weight:700;line-height:40px;padding:0 26px;letter-spacing:.3px}
.main-nav li.active{background:var(--teal-dark)}

/* hero */
.hero{height:455px;position:relative;background:linear-gradient(180deg,#d9d3cb 0%,#c8bdb0 55%,#8d7f72 100%)}
.slide-arrow{position:absolute;top:205px;width:34px;height:34px;border-radius:50%;background:var(--navy);display:flex;align-items:center;justify-content:center}
.slide-arrow.prev{left:40px}.slide-arrow.next{right:40px}

/* welcome */
.welcome{height:455px;text-align:center;padding-top:78px}
.section-title{font-size:31px;font-weight:700;color:var(--teal);letter-spacing:.5px}
.welcome p{font-size:12.5px;line-height:1.7;margin:10px auto 0;width:930px}
.btn-book{display:inline-block;margin-top:22px;background:var(--navy);color:var(--white);font-size:15px;font-weight:700;padding:11px 24px}
.note{font-size:16px;color:var(--ink);margin-top:20px}

/* services */
.services{height:735px;background:var(--navy);text-align:center;padding-top:78px}
.services .lead{color:var(--white);font-size:13px;margin-top:14px}
.service-grid{display:grid;grid-template-columns:repeat(4,220px);gap:22px 18px;width:936px;margin:28px auto 0}
.service-tile{height:200px;display:flex;flex-direction:column}
.service-tile .photo{flex:1}
.service-tile .label{height:36px;background:var(--teal);color:var(--white);font-size:13px;font-weight:700;line-height:36px;letter-spacing:.3px}
.btn-more{display:inline-block;margin-top:26px;background:var(--white);color:var(--navy);font-size:14px;font-weight:700;padding:11px 22px}

/* practitioners */
.practitioners{height:570px;text-align:center;padding-top:78px}
.practitioners .lead{font-size:13px;line-height:1.6;margin:12px auto 0;width:936px}
.team{display:grid;grid-template-columns:repeat(4,220px);gap:18px;width:936px;margin:46px auto 0}
.member .photo{height:220px;background:linear-gradient(180deg,#d6d6d6,#8f8f8f)}
.member .name{font-size:14px;font-weight:700;color:var(--navy);margin-top:20px;letter-spacing:.3px}
.member .role{font-size:14px;color:var(--navy)}

/* blog */
.blog{height:640px;background:var(--grey-bg);text-align:center;padding-top:78px;position:relative}
.blog-cards{display:grid;grid-template-columns:repeat(3,298px);gap:21px;width:936px;margin:30px auto 0;text-align:left}
.post{background:var(--white);height:440px}
.post .photo{height:190px}
.post .body{padding:22px 18px}
.post h3{font-size:16px;font-weight:600;color:var(--ink);line-height:1.3}
.post .date{font-size:10px;color:#777;margin-top:10px}
.post .excerpt{font-size:10px;line-height:1.6;color:#888;margin-top:12px}
.post .read{display:inline-block;margin-top:22px;border:1px solid #ccc;font-size:10px;color:#888;padding:8px 12px}
.blog-arrow{position:absolute;top:345px}
.blog-arrow.prev{left:48px}.blog-arrow.next{right:48px}

/* contact strip */
.contact-strip{height:90px;display:flex;justify-content:space-between;align-items:center;width:936px;margin:0 auto;font-size:14px;color:var(--ink)}
.contact-strip span{display:flex;align-items:center;gap:10px}

.map{height:340px;background:linear-gradient(135deg,#e8e6e2,#dcdad5)}

/* footer */
.site-footer{height:150px;background:var(--footer);color:#cfcfcf;font-size:11px;position:relative}
.site-footer .links{position:absolute;left:132px;top:40px;display:flex;gap:10px}
.site-footer .copy{position:absolute;left:132px;top:68px}
.social{position:absolute;left:1010px;top:42px;display:flex;gap:8px}
.social span{width:24px;height:24px;border-radius:50%;background:#3f7fc6}
</style>
</head>
<body>

<header class="site-header">
  <div class="brand"><span class="brand-dot"></span><span class="brand-name">Bayward Vale Physiotherapy</span></div>
  <div class="search">Search
    <svg width="14" height="14" viewBox="0 0 14 14"><circle cx="6" cy="6" r="4.5" fill="none" stroke="#555" stroke-width="1.6"/><line x1="9.3" y1="9.3" x2="13" y2="13" stroke="#555" stroke-width="1.8"/></svg>
  </div>
  <div class="contact-top">
    <div class="addr"><svg width="10" height="14" viewBox="0 0 10 14"><path d="M5 0a5 5 0 0 1 5 5c0 4-5 9-5 9S0 9 0 5a5 5 0 0 1 5-5z" fill="#2f3350"/><circle cx="5" cy="5" r="2" fill="#fff"/></svg>58-60 Harbour Parade, Bayward Vale VIC 3170</div>
    <div class="phone"><svg width="18" height="18" viewBox="0 0 18 18"><path d="M4 1l3 4-2 2c1 2 3 4 5 5l2-2 4 3-2 4C8 17 1 10 1 4z" fill="#2f3350"/></svg>03 9555 0142</div>
  </div>
</header>

<nav class="main-nav">
  <ul>
    <li class="active">HOME</li><li>ABOUT</li><li>SERVICES</li><li>CONDITIONS</li><li>HEALTH TIPS</li><li>BLOG</li><li>CONTACT</li>
  </ul>
</nav>

<section class="hero" role="img" aria-label="Runner training along a seaside promenade lined with lamp posts">
  <span class="slide-arrow prev"><svg width="12" height="12" viewBox="0 0 12 12"><path d="M8 1L3 6l5 5" fill="none" stroke="#fff" stroke-width="2.2"/></svg></span>
  <span class="slide-arrow next"><svg width="12" height="12" viewBox="0 0 12 12"><path d="M4 1l5 5-5 5" fill="none" stroke="#fff" stroke-width="2.2"/></svg></span>
</section>

<section class="welcome">
  <h1 class="section-title">WELCOME TO BAYWARD VALE PHYSIOTHERAPY</h1>
  <p>Bayward Vale Physiotherapy is an innovative physiotherapy practice offering comprehensive services by experienced and highly qualified physiotherapists.</p>
  <p>We achieve outstanding clinical results for a broad range of common conditions including: back pain, neck pain, headache, migraine, shoulder pain, sports injuries, vertigo, knee pain, incontinence, persistent pelvic pain and women's health and men's health issues.</p>
  <p>Our team of physiotherapists have extensive experience from working in private practice, private and public hospitals, and research and teaching over a range of physiotherapy disciplines including sports, manipulative, musculoskeletal, neurological, pain management, continence, women's / men's health and paediatric services.</p>
  <p>We are confident our practice will offer a service that stands apart, as we value excellence in quality care delivered by highly-educated and experienced physiotherapists.</p>
  <span class="btn-book">BOOK ONLINE HERE*</span>
  <p class="note">*Please note not all practitioners are available online – please call 95550142 to speak with our reception team.</p>
</section>

<section class="services">
  <h2 class="section-title">SERVICES</h2>
  <p class="lead">Our practice offers the following core services throughout Ashfield Rise, Kellan, Northmere, Reedy Flat, Corbury,</p>
  <div class="service-grid">
    <div class="service-tile"><div class="photo" role="img" aria-label="Physiotherapist treating a patient" style="background:linear-gradient(135deg,#efeae6,#b9a99b)"></div><div class="label">PHYSIOTHERAPY</div></div>
    <div class="service-tile"><div class="photo" role="img" aria-label="Couple running on a beach" style="background:linear-gradient(180deg,#a9c6d8,#d8c7ae)"></div><div class="label">WOMENS AND MENS HEALTH</div></div>
    <div class="service-tile"><div class="photo" role="img" aria-label="Sprinter at the starting line" style="background:linear-gradient(135deg,#f1c37a,#3d6f9d)"></div><div class="label">SPORTS</div></div>
    <div class="service-tile"><div class="photo" role="img" aria-label="Muscle anatomy illustration" style="background:linear-gradient(135deg,#e6b9a3,#b8614a)"></div><div class="label">MUSCULOSKELETAL</div></div>
    <div class="service-tile"><div class="photo" role="img" aria-label="Real time ultrasound assessment" style="background:linear-gradient(135deg,#d9a987,#8a5a42)"></div><div class="label">REAL TIME ULTRASOUND</div></div>
    <div class="service-tile"><div class="photo" role="img" aria-label="Relaxing massage with stones" style="background:linear-gradient(135deg,#e9ddd2,#b89581)"></div><div class="label">MASSAGE</div></div>
    <div class="service-tile"><div class="photo" role="img" aria-label="Back with highlighted lower back pain" style="background:linear-gradient(135deg,#7a5a4c,#3a2a25)"></div><div class="label">CHRONIC PAIN MANAGEMENT</div></div>
    <div class="service-tile"><div class="photo" role="img" aria-label="Person experiencing dizziness" style="background:linear-gradient(135deg,#c9c3bd,#7e7670)"></div><div class="label">VERTIGO MANAGEMENT</div></div>
  </div>
  <span class="btn-more">VIEW MORE</span>
</section>

<section class="practitioners">
  <h2 class="section-title">OUR PRACTITIONERS</h2>
  <p class="lead">All practitioners at our clinic have completed or are completing postgraduate university training and most are involved in teaching, university lecturing and research. This means that you are being treated by highly qualified people at the forefront of new developments in the management of musculoskeletal disorders</p>
  <div class="team">
    <div class="member"><div class="photo" role="img" aria-label="Portrait of Clare Whitby"></div><div class="name">CLARE WHITBY</div><div class="role">Director</div></div>
    <div class="member"><div class="photo" role="img" aria-label="Portrait of Dr Helen Marsh"></div><div class="name">DR HELEN MARSH</div><div class="role">Director</div></div>
    <div class="member"><div class="photo" role="img" aria-label="Portrait of Rebecca Tolland"></div><div class="name">REBECCA TOLLAND</div><div class="role">Director</div></div>
    <div class="member"><div class="photo" role="img" aria-label="Portrait of Sam Kirrow"></div><div class="name">SAM KIRROW</div><div class="role">B Pod M Physio</div></div>
  </div>
</section>

<section class="blog">
  <h2 class="section-title">BLOG</h2>
  <svg class="blog-arrow prev" width="14" height="22" viewBox="0 0 14 22"><path d="M11 2L3 11l8 9" fill="none" stroke="#999" stroke-width="2"/></svg>
  <svg class="blog-arrow next" width="14" height="22" viewBox="0 0 14 22"><path d="M3 2l8 9-8 9" fill="none" stroke="#999" stroke-width="2"/></svg>
  <div class="blog-cards">
    <article class="post">
      <div class="photo" role="img" aria-label="Iced cake topped with dried rose petals" style="background:linear-gradient(135deg,#f0d9d4,#d27a86)"></div>
      <div class="body">
        <h3>The 2017 BVP Bake-Off competition is heating up!</h3>
        <div class="date">November 29, 2017</div>
        <p class="excerpt">Our team met for a friendly baking contest this week. Each entry was judged on taste and look, and the results were close. Read on to see who took home the prize this year.</p>
        <span class="read">Read more</span>
      </div>
    </article>
    <article class="post">
      <div class="photo" role="img" aria-label="Shoulder exercise beside a panel listing study details" style="background:linear-gradient(90deg,#d7b39c 0%,#b58a72 35%,#6ccccc 35%,#6ccccc 100%)"></div>
      <div class="body">
        <h3>Wanted: volunteers for shoulder rehabilitation study</h3>
        <div class="date">November 29, 2017</div>
        <p class="excerpt">We are looking for adults with shoulder pain to join a home exercise study. Sessions run over twelve weeks and include free physiotherapy with regular progress checks.</p>
        <span class="read">Read more</span>
      </div>
    </article>
    <article class="post">
      <div class="photo" role="img" aria-label="Group attending a workshop around a table" style="background:linear-gradient(135deg,#d9c3a8,#7b6a5c)"></div>
      <div class="body">
        <h3>The Pelvic Floor – it's more than just kegels!</h3>
        <div class="date">November 2, 2017</div>
        <p class="excerpt">Pelvic floor health is about more than one exercise. Learn how breathing, posture and daily habits work together, and how our team can guide a plan that suits you.</p>
        <span class="read">Read more</span>
      </div>
    </article>
  </div>
</section>

<div class="contact-strip">
  <span><svg width="10" height="14" viewBox="0 0 10 14"><path d="M5 0a5 5 0 0 1 5 5c0 4-5 9-5 9S0 9 0 5a5 5 0 0 1 5-5z" fill="#2f3350"/><circle cx="5" cy="5" r="2" fill="#fff"/></svg>58-60 Harbour Parade, Bayward Vale VIC 3170</span>
  <span><svg width="14" height="14" viewBox="0 0 18 18"><path d="M4 1l3 4-2 2c1 2 3 4 5 5l2-2 4 3-2 4C8 17 1 10 1 4z" fill="#2f3350"/></svg>03 9555 0187</span>
  <span><svg width="16" height="12" viewBox="0 0 16 12"><rect width="16" height="12" fill="#2f3350"/><path d="M0 0l8 6 8-6" fill="none" stroke="#fff" stroke-width="1.3"/></svg>admin@oakmerepilatesandrehab.com.au</span>
</div>

<div class="map" role="img" aria-label="Street map showing the clinic location"></div>

<footer class="site-footer">
  <div class="links"><span>Home</span>|<span>About</span>|<span>Services</span>|<span>Conditions</span>|<span>Health Tips</span>|<span>Blog</span>|<span>Contact</span></div>
  <div class="copy">Copyright © 2018 Bayward Vale Physiotherapy. All rights reserved.</div>
  <div class="social"><span></span><span></span></div>
</footer>

</body>
</html>
```